Building technology company seek stationery design and folder design

Letterhead, and a folder design
ideally, I would have two letter head design, one is for one-page bussiness letter. the other one I can use for longer document such report, or analysis regular report page
you can find company logo and overall style at our website:
www.structavolt.example

we are in building technology business, using internet of things technology to improve building energy efficiency to make building greener.

Industry/Entity Type

It Company

Requirements
Must have
• company logo
Nice to have
• techy look abstract graphics, etc.
Should not have
• no comment

```html
<!DOCTYPE html>
<html lang="en">
<head>
<meta charset="utf-8">
<title>Structavolt Stationery</title>
<link href="https://fonts.googleapis.com/css2?family=Questrial&display=swap" rel="stylesheet">
<style>
  :root{
    --stage:#dcdcdc;
    --paper:#ffffff;
    --paper-shade:#eeeeee;
    --brand-green:#b1d44e;
    --brand-green-light:#c3de6e;
    --brand-green-dark:#9fc23d;
    --ink:#4a4a4a;
    --ink-soft:#6b6b6b;
    --white:#ffffff;
  }
  *{margin:0;padding:0;box-sizing:border-box;}
  html,body{width:1200px;height:821px;overflow:hidden;background:var(--stage);}
  body{position:relative;font-family:"Questrial",sans-serif;color:var(--ink);}

  /* Letterhead */
  .letterhead{position:absolute;left:74px;top:114px;width:441px;height:620px;background:var(--paper);overflow:hidden;}
  .letterhead-texture{position:absolute;inset:0;background:linear-gradient(100deg,var(--paper) 20%,var(--paper-shade) 100%);}
  .letterhead-edge{position:absolute;left:0;top:0;width:9px;height:100%;background:var(--brand-green);}
  .brand{position:absolute;display:flex;align-items:center;gap:6px;}
  .brand-mark{background:var(--brand-green);}
  .letterhead .brand{left:38px;top:58px;}
  .letterhead .brand-mark{width:14px;height:14px;}
  .letterhead .brand-name{font-size:12px;letter-spacing:1.2px;color:var(--brand-green);}
  .contact{position:absolute;left:314px;top:57px;list-style:none;font-size:6.5px;color:var(--ink);line-height:9px;}
  .contact li{display:flex;align-items:center;gap:4px;}
  .contact svg{width:6px;height:6px;fill:var(--brand-green);}
  .salutation{position:absolute;left:40px;top:174px;font-size:11.5px;color:var(--ink);}
  .letter-body{position:absolute;left:40px;top:213px;width:366px;font-size:6.1px;line-height:9.5px;color:var(--ink-soft);text-align:justify;}
  .letter-body p{margin-bottom:9.5px;}
  .closing{position:absolute;left:40px;top:406px;font-size:6.3px;color:var(--ink-soft);}
  .signature{position:absolute;left:36px;top:432px;width:80px;height:30px;background:linear-gradient(90deg,var(--brand-green-light),rgba(195,222,110,0));opacity:.6;}
  .footer-url{position:absolute;left:0;right:0;top:591px;text-align:center;font-size:7px;letter-spacing:1.4px;color:var(--ink);}

  /* Folder */
  .folder{position:absolute;left:553px;top:77px;width:520px;height:658px;background:var(--brand-green);overflow:hidden;}
  .folder-texture{position:absolute;inset:0;background:radial-gradient(circle at 30% 25%,var(--brand-green-light) 0%,rgba(195,222,110,0) 55%),radial-gradient(circle at 80% 80%,var(--brand-green-light) 0%,rgba(195,222,110,0) 50%);opacity:.7;}
  .folder-spine{position:absolute;left:6px;top:0;width:28px;height:100%;}
  .folder .brand{left:0;right:0;top:348px;justify-content:center;gap:10px;}
  .folder .brand-mark{width:26px;height:26px;background:var(--white);}
  .folder .brand-name{font-size:30px;letter-spacing:3px;color:var(--white);}
</style>
</head>
<body>

<section class="letterhead">
  <div class="letterhead-texture" role="img" aria-label="Faint grey network pattern of linked nodes across the page"></div>
  <div class="letterhead-edge"></div>

  <div class="brand">
    <span class="brand-mark"></span>
    <span class="brand-name">STRUCTAVOLT</span>
  </div>

  <ul class="contact">
    <li><svg viewBox="0 0 10 10"><path d="M2 0h2l1 3-1.5 1a6 6 0 0 0 2.5 2.5L7 5l3 1v2a2 2 0 0 1-2 2C4 10 0 6 0 2a2 2 0 0 1 2-2z"/></svg>(555) 010-4821</li>
    <li><svg viewBox="0 0 10 10"><rect x="0" y="2" width="10" height="7"/></svg>info@structavolt.example</li>
    <li><svg viewBox="0 0 10 10"><circle cx="5" cy="5" r="4"/></svg>structavolt</li>
  </ul>

  <p class="salutation">Dear Mr. Harlow,</p>

  <div class="letter-body">
    <p>Thank you for meeting with our team last week to review the energy profile of your office portfolio. As discussed, our sensor network tracks lighting, heating and cooling loads in real time and reports each change to a single dashboard. Early pilots show steady savings within the first quarter, with no disruption to tenants or daily building operations on site.</p>
    <p>We propose a phased rollout beginning with the two towers on Grant Street. Each floor will receive wireless meters, occupancy sensors and a gateway that links to our cloud platform. Your facility staff will gain alerts, weekly summaries and clear targets for each system, so small faults are caught before they grow into costly repairs or wasted power.</p>
    <p>Installation takes about three weeks per building and can be scheduled outside business hours. Our engineers will calibrate every device, train your team on the dashboard and stay on call during the first month. After that, quarterly reviews will compare results against the baseline we measured together, and we will suggest further steps, from schedule changes to equipment upgrades, that keep your buildings efficient and comfortable for years to come.</p>
    <p>Please find the full proposal, pricing and timeline attached to this letter. If you have questions about any part of the plan, our project lead will be glad to walk through the details with you and your board at a time that suits you.</p>
  </div>

  <p class="closing">Sincerely,</p>
  <div class="signature" role="img" aria-label="Handwritten green signature of Dana Harlow"></div>

  <p class="footer-url">www.structavolt.example</p>
</section>

<section class="folder">
  <div class="folder-texture" role="img" aria-label="Subtle light green network pattern of linked nodes across the cover"></div>
  <svg class="folder-spine" viewBox="0 0 28 658" preserveAspectRatio="none" aria-hidden="true">
    <line x1="3" y1="0" x2="3" y2="658" stroke="#c8e27a" stroke-width="1"/>
    <line x1="9" y1="0" x2="9" y2="658" stroke="#c8e27a" stroke-width="1"/>
    <line x1="27" y1="0" x2="27" y2="658" stroke="#c8e27a" stroke-width="1.2"/>
  </svg>
  <div class="brand">
    <span class="brand-mark"></span>
    <span class="brand-name">STRUCTAVOLT</span>
  </div>
</section>

</body>
</html>
```